Business Card Design

We need a business card designed for our new company. Prefer a black card with white logo & writing.

Contact Information for Business Card

Ted Galloway, address: 7-4812 Fernhollow Road, Abbotsford, BC, V3K 8R2, Office Phone: 604-712-3390, Cell: 604-947-2164, Email: ted@resinworkshub.ca

Colors

Designer to choose only greyscale colors for use in the design.

```html
<!DOCTYPE html>
<html lang="en">
<head>
<meta charset="UTF-8">
<title>Resinworks Hub – Business Card</title>
<link href="https://fonts.googleapis.com/css2?family=Poppins:wght@400;600;700&display=swap" rel="stylesheet">
<style>
  :root {
    --canvas: #3a3a3b;
    --card: #231f1e;
    --card-edge: #2c2827;
    --emboss: #3b3635;
    --white: #ffffff;
    --band: #4a4646;
    --band-line: #7a7676;
    --divider: #5e5958;
  }
  * { box-sizing: border-box; margin: 0; padding: 0; }
  html, body {
    width: 1200px; height: 689px; overflow: hidden;
    background: var(--canvas);
    font-family: "Poppins", sans-serif;
  }
  .stage {
    width: 1200px; height: 689px;
    display: flex; align-items: center; justify-content: center; gap: 40px;
  }
  .card {
    position: relative;
    width: 540px; height: 310px;
    background: var(--card);
    border-radius: 18px;
    overflow: hidden;
    box-shadow: 0 10px 30px rgba(0,0,0,0.35);
  }
  /* Front */
  .card-front .brand {
    position: absolute; inset: 0;
    display: flex; align-items: center; justify-content: center; gap: 16px;
  }
  .brand-dot {
    width: 26px; height: 26px; border-radius: 50%;
  }
  .brand-name {
    font-weight: 700; font-size: 38px; letter-spacing: 1px;
    text-transform: uppercase; line-height: 1;
  }
  .card-front .brand-dot { background: var(--emboss); }
  .card-front .brand-name { color: var(--emboss); }

  /* Back */
  .card-back .brand {
    position: absolute; left: 28px; top: 108px; width: 240px;
    display: flex; align-items: center; gap: 12px;
  }
  .card-back .brand-dot { background: var(--white); width: 18px; height: 18px; flex: none; }
  .card-back .brand-name { color: var(--white); font-size: 26px; line-height: 1.05; }

  .divider {
    position: absolute; left: 282px; top: 26px;
    width: 1px; height: 214px;
    background: linear-gradient(var(--card), var(--divider) 30%, var(--divider) 70%, var(--card));
  }
  .contact {
    position: absolute; left: 305px; top: 40px;
    color: var(--white);
  }
  .contact-name {
    font-weight: 700; font-size: 21px; text-transform: uppercase;
    letter-spacing: 0.5px; margin-bottom: 12px;
  }
  .contact-line {
    display: flex; align-items: center; gap: 8px;
    font-size: 13.5px; line-height: 20px;
  }
  .contact-line svg { width: 12px; height: 12px; flex: none; }
  .contact-address {
    margin-top: 14px; font-size: 13.5px; line-height: 20px;
  }
  .band {
    position: absolute; left: 0; right: 0; bottom: 0; height: 56px;
    background: var(--band);
    border-top: 2px solid var(--band-line);
  }
  .band::before {
    content: ""; position: absolute; left: 0; right: 0; top: 8px;
    height: 1px; background: var(--card);
  }
  .band-badge {
    position: absolute; right: 46px; bottom: 34px;
    width: 46px; height: 46px; border-radius: 50%;
    background: var(--white);
  }
</style>
</head>
<body>
<main class="stage">
  <section class="card card-front" aria-label="Card front">
    <div class="brand">
      <span class="brand-dot"></span>
      <span class="brand-name">Resinworks Hub</span>
    </div>
  </section>

  <section class="card card-back" aria-label="Card back">
    <div class="brand">
      <span class="brand-dot"></span>
      <span class="brand-name">Resinworks<br>Hub</span>
    </div>
    <div class="divider"></div>
    <div class="contact">
      <p class="contact-name">Ted Galloway</p>
      <p class="contact-line">
        <svg viewBox="0 0 24 24" fill="#fff"><path d="M6.6 10.8a15.1 15.1 0 0 0 6.6 6.6l2.2-2.2a1 1 0 0 1 1-.25 11.4 11.4 0 0 0 3.6.57 1 1 0 0 1 1 1V20a1 1 0 0 1-1 1A17 17 0 0 1 3 4a1 1 0 0 1 1-1h3.5a1 1 0 0 1 1 1c0 1.25.2 2.45.57 3.57a1 1 0 0 1-.25 1z"/></svg>
        604-712-3390
      </p>
      <p class="contact-line">
        <svg viewBox="0 0 24 24" fill="none" stroke="#fff" stroke-width="2"><rect x="6" y="2" width="12" height="20" rx="2"/><line x1="11" y1="18" x2="13" y2="18"/></svg>
        604-947-2164
      </p>
      <p class="contact-line">
        <svg viewBox="0 0 24 24" fill="#fff"><path d="M2 5h20v14H2z M3 6l9 7 9-7" stroke="#231f1e" stroke-width="1.5"/></svg>
        ted@resinworkshub.ca
      </p>
      <p class="contact-address">7-4812 Fernhollow Road,<br>Abbotsford, BC, V3K 8R2</p>
    </div>
    <div class="band"></div>
    <div class="band-badge"></div>
  </section>
</main>
</body>
</html>
```